Tollin Waste Website Design

Our new start-up needs a website design. We plan to help businesses find more sustainable ways to manage their waste. Our initial website aims to gather contact data from potential business customers and comprehensive information from waste facilities and waste transporters. We have a logo design (attached) which we would like included in the website design. I have also attached a number of pages that describe what information should appear on each page as well as a web design brief file that describes the look we are after.

```html
<!DOCTYPE html>
<html lang="en">
<head>
<meta charset="utf-8">
<title>Tollin Waste — Website Design</title>
<link href="https://fonts.googleapis.com/css2?family=Lato:wght@400;700;900&display=swap" rel="stylesheet">
<style>
  :root {
    --board-green: #9dcb2a;
    --brand-green: #5a9a1e;
    --brand-green-light: #7cbc2c;
    --brand-green-dark: #3f7a12;
    --photo-dark: #1c2530;
    --photo-mid: #3a4a58;
    --photo-warm: #4a3a30;
    --footer-bar: rgba(20, 22, 26, 0.88);
    --white: #ffffff;
    --ink: #2e2e2e;
    --field-bg: #f0f0f0;
    --field-border: #c9c9c9;
  }
  * { box-sizing: border-box; margin: 0; padding: 0; }
  html, body { width: 1058px; height: 1200px; overflow: hidden; }
  body {
    background: var(--board-green);
    font-family: "Lato", sans-serif;
    position: relative;
  }
  .screen {
    position: absolute;
    left: 70px;
    width: 918px;
    height: 565px;
    overflow: hidden;
  }
  .screen--home { top: 16px; }
  .screen--signup { top: 606px; }
  .hero-photo {
    position: absolute; inset: 0;
    background:
      radial-gradient(ellipse at 52% 40%, #5b6a55 0%, transparent 35%),
      radial-gradient(ellipse at 20% 30%, #6b6f70 0%, transparent 40%),
      radial-gradient(ellipse at 80% 75%, #2f4030 0%, transparent 45%),
      linear-gradient(160deg, var(--photo-mid) 0%, var(--photo-dark) 55%, var(--photo-warm) 100%);
  }
  .hero-shade { position: absolute; inset: 0; background: rgba(0,0,0,0.35); }
  .brand {
    position: absolute; left: 58px; top: 34px;
    display: flex; align-items: center; gap: 8px;
    color: var(--white); font-weight: 900; font-size: 24px; letter-spacing: 0.5px;
  }
  .brand__dot {
    width: 40px; height: 40px; border-radius: 50%;
    border: 3px solid var(--white);
  }
  .nav {
    position: absolute; top: 45px; left: 544px;
    display: flex; gap: 26px;
    list-style: none;
  }
  .nav li { color: var(--white); font-size: 10.5px; letter-spacing: 0.3px; }
  .hero-copy {
    position: absolute; top: 206px; left: 0; right: 0;
    text-align: center; color: var(--white);
  }
  .hero-copy h1 { font-weight: 900; font-size: 35px; line-height: 1.1; letter-spacing: 0.2px; }
  .hero-copy p { font-size: 23px; font-weight: 700; margin-top: 2px; }
  .audience {
    position: absolute; top: 298px; left: 123px;
    display: flex; gap: 10px;
  }
  .audience__btn {
    width: 217px; height: 57px;
    border: 2px solid var(--white); border-radius: 7px;
    background: linear-gradient(var(--brand-green-light), var(--brand-green-dark));
    color: var(--white); font-weight: 700; font-size: 19px;
    display: flex; align-items: center; justify-content: center;
  }
  .footer {
    position: absolute; left: 0; right: 0; bottom: 0; height: 52px;
    background: var(--footer-bar);
  }
  .footer__copy {
    position: absolute; left: 58px; top: 20px;
    color: var(--white); font-size: 10px;
  }
  .footer__badge {
    position: absolute; left: 435px; top: -22px;
    width: 46px; height: 46px; border-radius: 50%;
    background: var(--white); border: 4px solid var(--brand-green-light);
  }
  .social {
    position: absolute; right: 60px; top: 19px;
    display: flex; gap: 16px; list-style: none;
  }
  .social li { width: 15px; height: 15px; border-radius: 50%; background: var(--white); }
  .dim { position: absolute; inset: 0; background: rgba(0,0,0,0.62); }
  .modal {
    position: absolute; left: 194px; top: 154px;
    width: 529px; height: 272px;
    background: var(--white); border-radius: 6px;
    text-align: center;
  }
  .modal__close {
    position: absolute; left: 510px; top: 9px;
    font-weight: 900; font-size: 14px; color: var(--ink);
  }
  .modal h2 {
    margin-top: 36px; font-weight: 900; font-size: 29px; color: var(--ink);
  }
  .modal h2 span { color: var(--brand-green); }
  .modal__lead { font-size: 19px; font-weight: 700; color: var(--ink); margin-top: 4px; }
  .modal__ask { font-size: 16.5px; font-weight: 700; color: var(--brand-green-light); margin-top: 3px; }
  .modal__field {
    display: block; margin: 17px auto 0;
    width: 333px; height: 41px;
    border: 1.5px solid var(--field-border); border-radius: 7px;
    background: var(--field-bg);
    font: 400 15px "Lato", sans-serif; color: #555; text-align: center;
    line-height: 38px;
  }
  .modal__submit {
    display: block; margin: 8px auto 0;
    width: 333px; height: 41px; border-radius: 7px;
    background: linear-gradient(var(--brand-green-light), var(--brand-green-dark));
    color: var(--white); font-weight: 700; font-size: 19px; line-height: 41px;
  }
</style>
</head>
<body>

<section class="screen screen--home">
  <div class="hero-photo" role="img" aria-label="Worker sorting glass waste on a recycling plant conveyor"></div>
  <div class="hero-shade"></div>
  <div class="brand"><span class="brand__dot"></span>TOLLIN WASTE</div>
  <ul class="nav"><li>ABOUT US</li><li>WHAT WE DO</li><li>RESOURCES</li><li>CONTACT US</li></ul>
  <div class="hero-copy">
    <h1>WELCOME TO TOLLIN WASTE</h1>
    <p>Take control of your waste here</p>
  </div>
  <div class="audience">
    <div class="audience__btn">Waste Producers</div>
    <div class="audience__btn">Waste Facilities</div>
    <div class="audience__btn">Waste Transporters</div>
  </div>
  <footer class="footer">
    <span class="footer__badge"></span>
    <p class="footer__copy">Copyright © 2018 Company Name All rights Reserved</p>
    <ul class="social"><li></li><li></li><li></li><li></li><li></li></ul>
  </footer>
</section>

<section class="screen screen--signup">
  <div class="hero-photo" role="img" aria-label="Worker sorting glass waste on a recycling plant conveyor"></div>
  <div class="hero-shade"></div>
  <div class="brand"><span class="brand__dot"></span>TOLLIN WASTE</div>
  <ul class="nav"><li>ABOUT US</li><li>WHAT WE DO</li><li>RESOURCES</li><li>CONTACT US</li></ul>
  <div class="audience">
    <div class="audience__btn">Waste Producers</div>
    <div class="audience__btn">Waste Facilities</div>
    <div class="audience__btn">Waste Transporters</div>
  </div>
  <footer class="footer">
    <span class="footer__badge"></span>
    <p class="footer__copy">Copyright © 2018 Company Name All rights Reserved</p>
    <ul class="social"><li></li><li></li><li></li><li></li><li></li></ul>
  </footer>
  <div class="dim"></div>
  <div class="modal">
    <span class="modal__close">x</span>
    <h2>WELCOME TO <span>TOLLIN WASTE</span></h2>
    <p class="modal__lead">We are just getting started.</p>
    <p class="modal__ask">Please register your email address to receive updates from us.</p>
    <div class="modal__field">Enter Email Address</div>
    <div class="modal__submit">Sign Up</div>
  </div>
</section>

</body>
</html>
```